1 page A4 double sided Brochure Design Folded to envelope size. Interesting fold design would be co

Small family run guesthouse BnB in Blue Mountains Australia needs a new brochure showing different aspects of business

We need a new brochure to go with our new website. Basically the design would be good as a double sided brochure that can be folded down to standard envelope size.

We have seen a few interesting brochure designs before that fold in different ways (and therefore have the design to match) but still fold down to this size to help with postage.

The design would have to showcase the different aspects of our business including individual accommodation for couples and families, conference market, wedding market, retreat market and events market (parties, re-unions etc). The Business must be Showcased as The Fernhollow Lodge, Blue Mountains

It is possible to arrange design so folds separate different sections of info/pictures.

It is also optional that we possibly have 2 brochures instead, one that is a basic all inclusive once described and one that only deals with group bookings (wedding conference retreats etc etc)

Must match design elements from our web page. Feel free to take informations, elements and images from there for design www.fernhollowlodge.com.au

Here is a link to our view we wake up to every morning to inspire all those working on a design!
http://www.fernhollowlodge.com.au/images/view.jpg

Target Market(s)

Group bookings, weddings, conferences, retreats, events and Blue Mountains Travellers

Industry/Entity Type

Accommodation

Requirements
Must have
• Must be based on our current websites design feel, colours, etc
Must be showcased as The Fernhollow Lodge Blue Mountains.
Must mention The Blue Mountains as a world heritage destination
Must be A4 double sided that can fold down to 1/3 the size to fit into a standard envelope. Any designs that will not fit in a standard envelope once folded can not be accepted as they are outside the brief
Nice to have
• Interesting folding design to get people interested to read it.

```html
<!DOCTYPE html>
<html lang="en">
<head>
<meta charset="utf-8">
<title>The Fernhollow Lodge, Blue Mountains – Brochure Cover</title>
<link rel="stylesheet" href="https://fonts.googleapis.com/css2?family=Arimo:wght@400;700&display=swap">
<style>
  :root {
    --backdrop: #bdbdbd;
    --page: #000000;
    --band: #3a3a3a;
    --band-edge: #4a4a4a;
    --paper: #f2f2f2;
    --title: #e8e8e8;
    --subtitle: #bdbdbd;
    --body-text: #b9b9b9;
    --logo-panel: #d9ead0;
    --logo-ink: #1c1c1c;
    --frame: #f4f4f4;
    --ornament-band: #141414;
  }
  * { box-sizing: border-box; margin: 0; padding: 0; }
  html, body { width: 1200px; height: 750px; overflow: hidden; }
  body {
    background: var(--backdrop);
    font-family: "Arimo", Arial, sans-serif;
    position: relative;
  }
  .brochure-cover {
    position: absolute;
    left: 220px; top: 55px;
    width: 760px; height: 640px;
    background: var(--page);
    overflow: hidden;
    box-shadow: 0 8px 24px rgba(0,0,0,.25);
  }
  .mountain-band { position: absolute; left: 0; top: 0; width: 760px; height: 300px; }
  .cover-title {
    position: absolute; left: 110px; top: 34px;
    color: var(--title); font-size: 34px; font-weight: 400;
    letter-spacing: 1px; text-shadow: 0 1px 3px rgba(255,255,255,.25);
  }
  .cover-subtitle {
    position: absolute; left: 500px; top: 80px;
    color: var(--subtitle); font-size: 17px;
  }
  .paper-strip {
    position: absolute; left: 0; top: 175px; width: 120px; height: 100px;
    background: var(--paper);
  }
  .lodge-mark {
    position: absolute; left: 112px; top: 150px; width: 124px; height: 140px;
    background: var(--logo-panel); border: 3px solid var(--paper);
    display: flex; align-items: center; justify-content: center; text-align: center;
    color: var(--logo-ink); font-size: 17px; font-weight: 700; line-height: 1.25;
    padding: 8px;
  }
  .intro-text {
    position: absolute; left: 262px; top: 160px; width: 470px;
    color: var(--body-text); font-size: 13px; line-height: 1.45;
  }
  .divider {
    position: absolute; left: 0; top: 312px; width: 760px; height: 4px;
    background: var(--frame);
  }
  .tagline {
    position: absolute; left: 22px; top: 336px; width: 460px;
    color: var(--title); font-size: 13px; line-height: 1.4;
  }
  .photo {
    position: absolute; border: 5px solid var(--frame);
  }
  .photo-pool {
    left: 20px; top: 392px; width: 228px; height: 170px;
    background: linear-gradient(180deg, #6f9fd6 0%, #9b6a4c 40%, #7a5a3e 65%, #2f8fc8 82%, #1f6fa8 100%);
  }
  .photo-garden {
    left: 256px; top: 384px; width: 240px; height: 170px;
    background: linear-gradient(180deg, #5f95de 0%, #7f8f6a 35%, #4f6a34 60%, #8a7a4e 100%);
  }
  .photo-view {
    left: 504px; top: 376px; width: 236px; height: 164px;
    background: radial-gradient(circle at 55% 30%, #f4f2e6 0%, #a9b9c8 25%, #3b4a52 55%, #141a16 100%);
  }
  .ornament-band {
    position: absolute; left: 0; top: 574px; width: 760px; height: 56px;
    background: var(--ornament-band);
  }
</style>
</head>
<body>
  <main class="brochure-cover">
    <svg class="mountain-band" viewBox="0 0 760 300" aria-hidden="true">
      <path d="M232 300 L232 150 C300 120 340 118 390 110 C450 100 470 60 520 70 C580 82 610 40 660 30 C700 22 730 15 760 10 L760 280 Z" fill="var(--band)"/>
      <path d="M232 150 C300 120 340 118 390 110 C450 100 470 60 520 70 C580 82 610 40 660 30 C700 22 730 15 760 10" fill="none" stroke="var(--band-edge)" stroke-width="2"/>
    </svg>

    <h1 class="cover-title">THE FERNHOLLOW LODGE</h1>
    <p class="cover-subtitle">Blue Mountains</p>

    <div class="paper-strip"></div>
    <div class="lodge-mark">The Fernhollow Lodge Blue Mountains</div>

    <p class="intro-text">Located on 32 acres of pristine virgin bushland in the centre of world heritage listed national park land The Fernhollow Lodge is your perfect Blue Mountains accommodation whether you are looking for a quiet place to escape with someone special or a function or conference venue in the Blue Mountains for your next group escape or private, personal, specially tailored wedding.</p>

    <div class="divider"></div>

    <p class="tagline">The Fernhollow Lodge Blue Mountains is a small family<br>run guesthouse, bush retreat and function centre.</p>

    <div class="photo photo-pool" role="img" aria-label="Photo of the brick guesthouse with its swimming pool"></div>
    <div class="photo photo-garden" role="img" aria-label="Photo of the garden lawn with gum trees and flowering shrubs"></div>
    <div class="photo photo-view" role="img" aria-label="Photo of the morning sun over the Blue Mountains valley"></div>

    <div class="ornament-band" role="img" aria-label="Decorative grey swirl pattern band"></div>
  </main>
</body>
</html>
```